New hardcover book cover

I want a striking, eye-catching cover with title, subtitle and a picture.See for previous book covers: www.brightquillpress.com

Target Market(s)

young, successful entrepreneurs that have built a business in a niche market that they discovered.

Font styles to use
Serif

Colors

Designer to choose colors to be used in the design.

Requirements
Must have
• A book cover that impresses and captures the imagination of those who look at it.
• MY MISTAKE, SORRY.
• Title: Founders Behind the Quiet Trade Boom
• Subtitle: 25 stories of success from
• discovering hidden opportunities
• Author: Dennis Harlow
• Please use the photo attached, thanks.

```html
<!DOCTYPE html>
<html lang="en">
<head>
<meta charset="utf-8">
<title>Founders Behind the Quiet Trade Boom — Dennis Harlow</title>
<link href="https://fonts.googleapis.com/css2?family=Raleway:wght@200;400&family=Montserrat:wght@900&display=swap" rel="stylesheet">
<style>
  :root {
    --navy: #14182a;
    --slate: #3a4458;
    --sky: #8fb4d6;
    --sky-light: #dbe7f1;
    --target-red: #c12a48;
    --title-red: #a8253a;
    --white: #ffffff;
  }
  * { margin: 0; padding: 0; box-sizing: border-box; }
  html, body { width: 764px; height: 1200px; overflow: hidden; background: var(--navy); }
  .cover {
    position: relative;
    width: 764px;
    height: 1200px;
    overflow: hidden;
    color: var(--white);
  }
  .cover-art {
    position: absolute;
    inset: 0;
    background:
      radial-gradient(ellipse 300px 420px at 70px 560px, var(--target-red) 0%, rgba(193,42,72,0.85) 55%, rgba(193,42,72,0) 100%),
      linear-gradient(115deg, var(--navy) 0%, #23283a 35%, var(--slate) 55%, #6f8aa8 72%, var(--sky) 85%, var(--sky-light) 100%);
  }
  .author {
    position: absolute;
    top: 88px;
    left: 0;
    width: 100%;
    text-align: center;
    font-family: "Raleway", sans-serif;
    font-weight: 200;
    font-size: 44px;
    letter-spacing: 0.16em;
    text-transform: uppercase;
  }
  .title {
    position: absolute;
    top: 742px;
    left: 0;
    width: 100%;
    font-family: "Montserrat", sans-serif;
    font-weight: 900;
    text-transform: uppercase;
    line-height: 1;
    text-align: center;
  }
  .title-line { display: flex; justify-content: center; align-items: center; }
  .title-line--first { font-size: 60px; letter-spacing: -0.02em; }
  .title-line--second { margin-top: 12px; font-size: 64px; letter-spacing: -0.02em; }
  .title-stack {
    display: flex;
    flex-direction: column;
    font-size: 20px;
    line-height: 0.95;
    margin-right: 8px;
    text-align: left;
  }
  .title-line--third { margin-top: 12px; font-size: 68px; letter-spacing: -0.02em; }
  .title-rule {
    width: 70px;
    height: 7px;
    background: var(--white);
    margin: 0 26px;
  }
  .title-line--fourth {
    margin-top: 10px;
    font-size: 96px;
    letter-spacing: -0.03em;
    color: var(--title-red);
  }
  .subtitle {
    position: absolute;
    top: 1108px;
    left: 0;
    width: 100%;
    text-align: center;
    font-family: "Raleway", sans-serif;
    font-weight: 400;
    font-size: 23px;
    line-height: 1.45;
    text-transform: uppercase;
  }
</style>
</head>
<body>
  <main class="cover">
    <div class="cover-art" role="img" aria-label="Close-up photograph of an arrow striking the red centre of an archery target against a blue sky"></div>

    <p class="author">Dennis Harlow</p>

    <h1 class="title">
      <span class="title-line title-line--first">Founders</span>
      <span class="title-line title-line--second">
        <span class="title-stack"><span>Behind</span><span>the</span></span>Quiet
      </span>
      <span class="title-line title-line--third">
        <span class="title-rule"></span>Trade<span class="title-rule"></span>
      </span>
      <span class="title-line title-line--fourth">Boom</span>
    </h1>

    <p class="subtitle">25 captivating stories of success<br>from discovering hidden opportunities</p>
  </main>
</body>
</html>
```